Business Card Design - Photographer

I am a landscape photographer and I require a business card design. 

I require two designs:
1)  a double sided business card
 and
b)  a single sided business card 

The single sided design can either be the same as the double sided (with just one side having all the information)....or it can be an entire new design. Its up to you.

My corporate colours are (CMYK):

Blue   69, 32, 0, 0
Grey  72,  64,  47,  31
Green  32,  2,  91,  0
Yellow   0, 19, 92, 0
Orange  0, 39, 75, 0

Colour space in final file should be in CMYK.

The details that need to be included on the card:

- Use the provided Logo
- Name: Wiktor Baranowski
- Email:   sales@vistalumeworks.com.au
- Website:    vistalumeworks.com.au
- Twitter:    twitter.com/vistalumeworks
- Facebook:   facebook.com/vistalumeworks
- Mobile  0417 539 662

Please use the attached template to design the logo to the specified size, including the marked bleed lines. I have also attached my logo in PNG (transparent background) and ai format for you to use.

The final file should be:
- Photoshop version with layers so I can edit the name/text etc. All non vector files should be high resolution at 1039 x 697 pixels at 300 dpi.

I also require a file as:
- Vector based PDF

Anyway questions please contact me.

Thank you

Industry/Entity Type

Landscape

Logo styles of interest
Pictorial/Combination Logo
Abstract Logo
Wordmark Logo
Lettermark Logo
Requirements
Must have
• The details that need to be included on the card:

- Use the provided Logo
- Name: Wiktor Baranowski
- Email: sales@vistalumeworks.com.au
- Website: vistalumeworks.com.au
- Twitter: twitter.com/vistalumeworks
- Facebook: facebook.com/vistalumeworks
- Mobile 0417 539 662

```html
<!DOCTYPE html>
<html lang="en">
<head>
<meta charset="utf-8">
<title>Vista Lume Works – Business Cards</title>
<link rel="stylesheet" href="https://fonts.googleapis.com/css2?family=Cinzel:wght@400&family=Bebas+Neue&family=Oswald:wght@400;500&display=swap">
<style>
  :root {
    --blue: #3a8ccc;
    --grey: #363d4f;
    --green: #a6c832;
    --yellow: #f5c400;
    --orange: #f39b3f;
    --card: #fbfbfb;
    --backdrop: #e4e5e8;
  }
  * { box-sizing: border-box; margin: 0; padding: 0; }
  html, body { width: 1200px; height: 840px; overflow: hidden; }
  body { background: var(--backdrop); position: relative; }

  .card {
    position: absolute;
    width: 600px;
    height: 360px;
    background: var(--card);
    box-shadow: 0 6px 18px rgba(0,0,0,.18);
    overflow: hidden;
  }
  .card--front { left: 80px; top: 50px; }
  .card--back  { left: 520px; top: 430px; }

  .brand { display: flex; flex-direction: column; align-items: center; }
  .brand__mark {
    width: 64px; height: 64px; border-radius: 50%;
    background: var(--grey);
  }
  .brand__name {
    font-family: "Cinzel", serif;
    color: var(--grey);
    letter-spacing: .04em;
    white-space: nowrap;
  }

  /* Front */
  .card--front .brand { position: absolute; left: 0; right: 0; top: 62px; }
  .card--front .brand__mark { width: 96px; height: 96px; margin-bottom: 22px; }
  .card--front .brand__name { font-size: 36px; padding: 0 6px 4px; border-bottom: 1.5px solid var(--grey); }
  .tagline {
    font-family: "Cinzel", serif; font-size: 13px; letter-spacing: .3em;
    color: var(--grey); margin-top: 8px;
  }
  .website {
    font-family: "Oswald", sans-serif; font-weight: 500; font-size: 22px;
    color: var(--blue); margin-top: 14px; letter-spacing: .01em;
  }
  .swoosh { position: absolute; left: 0; bottom: 0; width: 600px; height: 70px; }

  /* Back */
  .card--back .brand { position: absolute; left: 60px; top: 28px; width: 300px; }
  .card--back .brand__mark { width: 72px; height: 72px; margin-bottom: 14px; }
  .card--back .brand__name { font-size: 24px; }

  .contact {
    position: absolute; left: 200px; top: 212px;
    padding-left: 20px;
    border-left: 13px solid var(--yellow);
  }
  .contact__role {
    font-family: "Oswald", sans-serif; font-weight: 500; font-size: 20px;
    color: var(--green); line-height: 1;
  }
  .contact__name {
    font-family: "Bebas Neue", sans-serif; font-size: 50px; line-height: .95;
    color: var(--grey); border-bottom: 1.5px solid var(--grey); padding-bottom: 2px;
    white-space: nowrap;
  }
  .contact__name .first { color: var(--blue); }
  .contact__line {
    font-family: "Oswald", sans-serif; font-size: 13px; color: var(--grey);
    line-height: 1.55; white-space: nowrap; text-transform: uppercase;
  }
  .contact__line .label { color: var(--blue); }
  .contact__line .sep { margin: 0 6px; }
</style>
</head>
<body>

  <section class="card card--front" aria-label="Card front">
    <div class="brand">
      <span class="brand__mark"></span>
      <span class="brand__name">Vista Lume Works</span>
      <span class="tagline">FINE ART PHOTOGRAPHY</span>
      <span class="website">WWW.VISTALUMEWORKS.COM.AU</span>
    </div>
    <svg class="swoosh" viewBox="0 0 600 70" preserveAspectRatio="none" aria-hidden="true">
      <path d="M0 62 Q 300 58 600 0 L600 70 L0 70 Z" fill="var(--blue)"/>
      <path d="M0 66 Q 300 62 600 6 L600 70 L0 70 Z" fill="var(--blue)" opacity=".6"/>
    </svg>
  </section>

  <section class="card card--back" aria-label="Card back">
    <div class="brand">
      <span class="brand__mark"></span>
      <span class="brand__name">Vista Lume Works</span>
    </div>

    <div class="contact">
      <p class="contact__role">ART PHOTOGRAPHY</p>
      <h1 class="contact__name"><span class="first">WIKTOR</span> BARANOWSKI</h1>
      <p class="contact__line">0417 539 662 <span class="label">[mobile]</span><span class="sep">|</span>sales@vistalumeworks.com.au <span class="label">[email]</span></p>
      <p class="contact__line">facebook.com/vistalumeworks<span class="sep">|</span>@vistalumeworks <span class="label">[twitter]</span></p>
    </div>
  </section>

</body>
</html>
```